VIP Card Design Project

uZorvo is a premium sneaker store selling brand name sneakers like Volta, Rexa, Kembro and etc. ( www.uzorvoshop.com ) We need to design a VIP card to promote one of our discount program called "Uzorvo VIP Band 17", which offers 24% discount off all full-priced items. The idea is because we have a "Peakline Gym center" (peaklinegym.com) next door and we are trying to design a discount program for people going to the fitness center.
The design is for the front of the card. The back will be black and white with benefits information and member information.
The front design need to include our logo, "VIP", "Band 17" and our web address "Uzorvo.com" and Chatterly and quibbr logo.
It will be a plastic card in the size of 3.375x2.125 (bleed size 3.5x2.25)

```html
<!DOCTYPE html>
<html lang="en">
<head>
<meta charset="utf-8">
<title>Uzorvo VIP Band 17 – Member Card</title>
<link rel="stylesheet" href="https://fonts.googleapis.com/css2?family=Arimo:ital,wght@0,400;0,700;1,700&display=swap">
<style>
  :root {
    --backdrop: #ece7df;
    --gold-dark: #9a7d08;
    --gold-mid: #c9a80f;
    --gold-light: #f3df3a;
    --panel: #fbfaf6;
    --panel-shade: #ece9e0;
    --brand-green: #3cb44a;
    --club-orange: #f39019;
    --club-outline: #4a2a05;
    --discount-red: #e8262a;
    --ink: #111111;
    --benefit-text: #b8961a;
    --photo-frame: #e0393b;
    --social-blue: #3b6fb6;
    --social-sky: #35a9df;
    --watermark: #f8d9c0;
  }
  * { box-sizing: border-box; margin: 0; padding: 0; }
  html, body { width: 1200px; height: 665px; overflow: hidden; }
  body {
    background: var(--backdrop);
    font-family: "Arimo", Arial, sans-serif;
    position: relative;
  }
  .card {
    position: absolute;
    top: 150px;
    width: 540px;
    height: 350px;
    border-radius: 22px;
    background: linear-gradient(120deg, var(--gold-dark) 0%, var(--gold-mid) 35%, var(--gold-light) 65%, var(--gold-mid) 85%, var(--gold-dark) 100%);
    box-shadow: 0 6px 14px rgba(0,0,0,0.25);
    overflow: hidden;
  }
  .card--front { left: 40px; }
  .card--back { left: 620px; }
  .card__panel {
    position: absolute;
    top: 14px; left: 14px; right: 14px; bottom: 34px;
    background: radial-gradient(ellipse at 40% 35%, var(--panel) 55%, var(--panel-shade) 100%);
    border-radius: 46px 14px 60px 14px;
  }
  .card__web {
    position: absolute;
    right: 24px; bottom: 9px;
    color: #fff;
    font-size: 12px;
    display: flex; align-items: center; gap: 5px;
  }
  .card__web .dot { width: 9px; height: 9px; border-radius: 50%; background: #fff; }

  /* front */
  .brand-name {
    position: absolute;
    left: 52px; top: 22px;
    font-size: 86px; font-weight: 700;
    color: var(--brand-green);
    letter-spacing: 1px;
    line-height: 1;
  }
  .club-title {
    position: absolute;
    left: 50px; top: 128px;
    font-size: 24px; font-weight: 700; font-style: italic;
    color: var(--club-orange);
    -webkit-text-stroke: 1px var(--club-outline);
  }
  .product {
    position: absolute;
    border: 1.5px solid var(--photo-frame);
    box-shadow: 1px 1px 3px rgba(0,0,0,0.3);
  }
  .product--one { left: 60px; top: 200px; width: 108px; height: 70px; background: linear-gradient(135deg, #2d2d33, #c8322a 60%, #e6e6e6); }
  .product--two { left: 210px; top: 175px; width: 112px; height: 68px; background: linear-gradient(135deg, #d8452a, #f4f1ea 50%, #2b63b0); }
  .product--three { left: 345px; top: 110px; width: 76px; height: 60px; background: linear-gradient(135deg, #8a7a6a, #f1efec 50%, #d63a30); }
  .social {
    position: absolute;
    left: 440px;
    display: flex; align-items: center; gap: 5px;
    font-size: 11px; font-weight: 700; color: var(--ink);
  }
  .social .mark { width: 14px; height: 14px; border-radius: 3px; }
  .social--quibbr { top: 108px; }
  .social--quibbr .mark { background: var(--social-sky); }
  .social--chatterly { top: 140px; }
  .social--chatterly .mark { background: var(--social-blue); }
  .offer {
    position: absolute;
    left: 175px; top: 274px;
    font-size: 12px; font-weight: 700; letter-spacing: 1px;
    color: var(--ink);
  }
  .offer strong { color: var(--discount-red); font-size: 20px; }

  /* back */
  .back-mark {
    position: absolute;
    right: 24px; top: 18px;
    font-size: 54px; font-weight: 700;
    color: var(--watermark);
    opacity: 0.8;
  }
  .benefits {
    position: absolute;
    left: 30px; top: 40px; right: 30px;
    color: var(--benefit-text);
    font-size: 11.5px; line-height: 1.35;
  }
  .benefits h2 { color: var(--ink); font-size: 17px; margin-bottom: 6px; }
  .benefits p { margin-bottom: 6px; }
  .benefits ol { list-style: lower-alpha; padding-left: 30px; }
  .benefits li { margin-bottom: 7px; }
  .member-field {
    position: absolute;
    font-size: 12px; color: var(--ink);
    display: flex; align-items: flex-end; gap: 4px;
  }
  .member-field .line { border-bottom: 1px solid #888; display: inline-block; height: 12px; }
  .member-field--name { left: 60px; bottom: 8px; }
  .member-field--name .line { width: 170px; }
  .member-field--id { right: 24px; bottom: 40px; }
  .member-field--id .line { width: 90px; }
</style>
</head>
<body>
  <section class="card card--front" aria-label="Card front">
    <div class="card__panel">
      <div class="brand-name">uZorvo</div>
      <div class="club-title">Uzorvo VIP Band 17</div>
      <div class="product product--three" role="img" aria-label="Photo of a white and red high-top sneaker"></div>
      <div class="product product--one" role="img" aria-label="Photo of black and red running sneakers"></div>
      <div class="product product--two" role="img" aria-label="Photo of a white basketball sneaker with orange and blue accents"></div>
      <div class="social social--quibbr"><span class="mark"></span>quibbr</div>
      <div class="social social--chatterly"><span class="mark"></span>Chatterly</div>
      <div class="offer"><strong>24%</strong> discount off all full-priced items.</div>
    </div>
    <div class="card__web"><span class="dot"></span>www.Uzorvo.com</div>
  </section>

  <section class="card card--back" aria-label="Card back">
    <div class="card__panel">
      <div class="back-mark" aria-hidden="true">uZorvo</div>
      <div class="benefits">
        <h2>Benefits:</h2>
        <p>The UZORVO Member Program entitles Members to the following benefits:</p>
        <ol>
          <li>20% OFF your entire first purchase after you sign up (Limited Time Offer). Certain items are excluded from this offer. Please see stores for details.</li>
          <li>10% OFF every purchase while being a member. Certain items are excluded from this offer. Please see stores for details.</li>
          <li>Additional 10% OFF and FREE SHIPPING when an item is out of stock in store but can be shipped to you from another location.</li>
          <li>Eligible to purchase exclusive items offered to members only. Purchasing of exclusive items is limited to 1 item per member per 30 days. Please see stores for details.</li>
        </ol>
      </div>
      <div class="member-field member-field--name">Member Name : <span class="line"></span></div>
    </div>
    <div class="member-field member-field--id">Member ID : <span class="line"></span></div>
    <div class="card__web"><span class="dot"></span>www.Uzorvo.com</div>
  </section>
</body>
</html>
```